Business Card Design for BrightvaleMedia.com

--I need a business card design for my company BrightvaleMedia.com

I have attached my logo...I want the brightvale media logo on the front of the business card, and then I want The Quillstone Chief on the back of it with my information.

I would like to see a light colored background as well as a dark colored background

FRONT:
BRIGHTVALE MEDIA LOGO
248 N. Larkmoor
3rd Floor
San Diego CA 92173
www.BrightvaleMedia.com

Advanced Website & App Development
Websites, Apps, Online Voucher Systems

Leading Edge Marketing Services
SMS, VB, SMM, SEM,

BACK:
QUILLSTONE CHIEF LOGO
Dorian Pelletta
The Quillstone Chief
Call Or Text: 619-555-0148
Dorian@QuillstoneChief.example
www.QuillstoneChief.example

Target Market(s)

small business owners

Industry/Entity Type

Business Consultant

Contact Information for Business Card

FRONT:
BRIGHTVALE MEDIA LOGO
248 N. Larkmoor
3rd Floor
San Diego CA 92173
www.BrightvaleMedia.com

SMS, VB, SMM, SEM,

BACK:
QUILLSTONE CHIEF LOGO
Dorian Pelletta
The Quillstone Chief
Dorian@QuillstoneChief.example
www.QuillstoneChief.example

Requirements
Must have
• add this quote on it somewhere, anywhere,preferrably on back
• "The Fastest Way To Success Is To Take Action”
• — Dorian Pelletta, Quillstone Chief
Nice to have
• open
Should not have
• red

```html
<!DOCTYPE html>
<html lang="en">
<head>
<meta charset="utf-8">
<title>Brightvale Media Business Card</title>
<link rel="stylesheet" href="https://fonts.googleapis.com/css2?family=Open+Sans:wght@400;600;700&display=swap">
<style>
  :root {
    --stage: #141414;
    --card-light: #ffffff;
    --card-dark: #0a70a9;
    --brand-blue: #0d6ba6;
    --ink-grey: #5d5d5d;
    --ink-white: #ffffff;
  }
  html, body {
    margin: 0;
    padding: 0;
    width: 1200px;
    height: 900px;
    overflow: hidden;
    background: var(--stage);
    font-family: "Open Sans", Arial, sans-serif;
  }
  .stage {
    position: relative;
    width: 1200px;
    height: 900px;
  }
  .card {
    position: absolute;
    top: 306px;
    height: 271px;
    border-radius: 12px;
    overflow: hidden;
  }
  .card--personal {
    left: 149px;
    width: 439px;
    background: var(--card-light);
  }
  .card--company {
    left: 608px;
    width: 441px;
    background: var(--card-dark);
    color: var(--ink-white);
    text-align: center;
  }
  .personal-brand {
    position: absolute;
    left: 25px;
    top: 120px;
    margin: 0;
    color: var(--brand-blue);
    font-weight: 600;
    font-size: 18px;
    line-height: 24px;
    letter-spacing: 1px;
    white-space: nowrap;
  }
  .contact {
    position: absolute;
    left: 248px;
    top: 80px;
  }
  .contact__name {
    margin: 0;
    color: var(--brand-blue);
    font-weight: 700;
    font-size: 15px;
    line-height: 20px;
  }
  .contact__title {
    margin: 0 0 28px;
    color: var(--ink-grey);
    font-size: 12px;
    line-height: 16px;
  }
  .contact__list {
    list-style: none;
    margin: 0;
    padding: 0;
  }
  .contact__item {
    display: flex;
    align-items: center;
    color: var(--ink-grey);
    font-size: 11px;
    line-height: 16px;
    white-space: nowrap;
  }
  .contact__icon {
    width: 9px;
    height: 9px;
    margin-right: 7px;
    fill: var(--brand-blue);
    flex: none;
  }
  .quote {
    position: absolute;
    left: 25px;
    right: 25px;
    bottom: 16px;
    margin: 0;
    color: var(--ink-grey);
    font-size: 10px;
    line-height: 14px;
    text-align: center;
  }
  .quote cite {
    display: block;
    font-style: normal;
    color: var(--brand-blue);
  }
  .company-brand {
    margin: 36px 0 0;
    font-weight: 400;
    font-size: 30px;
    line-height: 34px;
    letter-spacing: 3px;
    color: var(--ink-white);
  }
  .company-info {
    margin: 36px 0 0;
    font-size: 12px;
    line-height: 16px;
  }
  .company-info p { margin: 0; }
  .company-info .web { margin-top: 10px; }
  .company-info .services { margin-top: 12px; }
  .company-info .marketing { margin-top: 6px; }
  .company-info strong { font-weight: 600; }
</style>
</head>
<body>
<main class="stage">
  <section class="card card--personal" aria-label="Back of card">
    <h2 class="personal-brand">QUILLSTONE CHIEF</h2>
    <div class="contact">
      <p class="contact__name">Dorian Pelletta</p>
      <p class="contact__title">The Quillstone Chief</p>
      <ul class="contact__list">
        <li class="contact__item">
          <svg class="contact__icon" viewBox="0 0 10 10" aria-hidden="true"><path d="M2 0.5 L3.6 2.6 L2.7 3.6 Q3.8 6 6.4 7.3 L7.4 6.4 L9.5 8 L8.3 9.5 Q1.5 8.5 0.5 1.7 Z"/></svg>
          619-555-0148
        </li>
        <li class="contact__item">
          <svg class="contact__icon" viewBox="0 0 10 10" aria-hidden="true"><path d="M0.5 2 H9.5 V8.5 H0.5 Z M0.5 2 L5 5.5 L9.5 2" stroke="#fff" stroke-width="0.8"/></svg>
          Dorian@QuillstoneChief.example
        </li>
        <li class="contact__item">
          <svg class="contact__icon" viewBox="0 0 10 10" aria-hidden="true"><circle cx="5" cy="5" r="4.6"/><path d="M0.6 5 H9.4 M5 0.4 Q2.5 5 5 9.6 M5 0.4 Q7.5 5 5 9.6" stroke="#fff" stroke-width="0.6" fill="none"/></svg>
          www.QuillstoneChief.example
        </li>
      </ul>
    </div>
    <blockquote class="quote">
      “The Fastest Way To Success Is To Take Action”
      <cite>— Dorian Pelletta, Quillstone Chief</cite>
    </blockquote>
  </section>

  <section class="card card--company" aria-label="Front of card">
    <h1 class="company-brand">BRIGHTVALE MEDIA</h1>
    <div class="company-info">
      <p>248 N. Larkmoor 3rd Floor, San Diego CA 92173</p>
      <p class="web">www.BrightvaleMedia.com</p>
      <p class="services">Advanced Website &amp; App Development | Websites | Apps<br>Online Voucher Systems</p>
      <p class="marketing"><strong>Leading Edge Marketing Services :</strong> SMS | VB | SMM | SEM,</p>
    </div>
  </section>
</main>
</body>
</html>
```